Norrell Advisory WA Business Card

Create an interesting, eye catching and colourful two sided business card. We are a business consulting operation assisting SME's improve all areas of their business. We provide consulting services to assist SME's to create a culture of continuous improvement, making a positive difference in the business. Our tag line is Small changes, big rewards. We want to create a well recognised, innovative brand that can be continued throughout our website, social media and email correspondence.

Target Market(s)

Small to Medium Enterprise Business Owners

Industry/Entity Type

Business Consultant

Contact Information for Business Card

Name of Business: Norrell Advisory - Steady Steps Lasting Gains
Derek Holloway Ph 0407385510 Megan Holloway Ph 0407913847
Email norrelladvisorywa@mailbox-example.com
Web address TBA
FaceBook page TBA

BACKSIDE OF CARD

Providing assistance with:

• Organisation & Efficiency
• Revenue generation & Marketing
• Financial Management
• Production quality & delivery
• Systems & Process documentation
• Exit Strategy

Font styles to use
Other font styles liked:
• Calibri

Colors

Designer to choose colors to be used in the design.

Requirements
Must have
• Calibri font

```html
<!DOCTYPE html>
<html lang="en">
<head>
<meta charset="utf-8">
<title>Norrell Advisory WA Business Card</title>
<link rel="stylesheet" href="https://fonts.googleapis.com/css2?family=Open+Sans:ital,wght@0,400;0,600;0,700;1,700&display=swap">
<style>
  :root {
    --page-bg: #2d2d2d;
    --card-white: #ffffff;
    --brand-blue: #0a76b8;
    --brand-blue-light: #3a9fd3;
    --brand-blue-deep: #0b6fb0;
    --ink-dark: #2f2f2f;
    --ink-mid: #4a4a4a;
    --ink-soft: #5a5a5a;
    --rule-grey: #c9c9c9;
    --band-dark: #2c3e4c;
  }
  * { box-sizing: border-box; margin: 0; padding: 0; }
  html, body {
    width: 1125px; height: 1200px; overflow: hidden;
    background: var(--page-bg);
    font-family: "Open Sans", sans-serif;
  }
  .card {
    position: absolute; left: 157px; width: 826px; height: 472px;
  }
  /* front */
  .card-front { top: 106px; background: var(--card-white); }
  .brand-block {
    position: absolute; left: 0; width: 414px; top: 262px;
    text-align: center;
  }
  .brand-name {
    display: inline-flex; align-items: center; gap: 12px;
    font-weight: 700; font-size: 26px; color: var(--ink-dark); letter-spacing: 0.2px;
    text-transform: uppercase; line-height: 1.2;
  }
  .brand-mark { width: 20px; height: 20px; background: var(--brand-blue); }
  .brand-tagline {
    margin-top: 2px; font-size: 15px; color: var(--ink-mid);
    letter-spacing: 2px; text-transform: uppercase;
  }
  .divider {
    position: absolute; left: 414px; top: 90px; width: 2px; height: 265px;
    background: linear-gradient(to bottom, rgba(201,201,201,0), var(--rule-grey) 25%, var(--rule-grey) 75%, rgba(201,201,201,0));
  }
  .people { position: absolute; left: 457px; top: 108px; }
  .person-name { font-weight: 600; font-size: 27px; line-height: 1.15; color: var(--brand-blue); }
  .person-phone { font-weight: 700; font-size: 16px; line-height: 1.2; color: var(--ink-mid); margin-bottom: 14px; }
  .contact-list { position: absolute; left: 457px; top: 253px; list-style: none; }
  .contact-item {
    display: flex; align-items: center; gap: 11px;
    font-size: 16px; color: var(--ink-soft); height: 25px; white-space: nowrap;
  }
  .contact-icon { width: 17px; height: 17px; flex: none; }
  .contact-square { width: 14px; height: 14px; background: var(--brand-blue); margin: 0 1.5px; flex: none; }
  .front-rule { position: absolute; left: 0; right: 0; top: 444px; height: 2px; background: var(--band-dark); }
  .front-band {
    position: absolute; left: 0; right: 0; top: 448px; height: 24px;
    background: linear-gradient(to right, var(--brand-blue), var(--brand-blue-light) 50%, var(--brand-blue));
  }
  /* back */
  .card-back {
    top: 639px;
    background: radial-gradient(ellipse at 50% 55%, #48a9dc 0%, var(--brand-blue-deep) 75%);
    color: #fff;
  }
  .back-brand {
    position: absolute; left: 0; right: 0; top: 160px; text-align: center;
    font-weight: 700; font-size: 44px; letter-spacing: 0.5px;
  }
  .services-heading {
    position: absolute; left: 63px; right: 63px; top: 343px;
    display: flex; align-items: center; gap: 6px;
    font-style: italic; font-weight: 700; font-size: 25px; white-space: nowrap;
  }
  .services-heading::before, .services-heading::after {
    content: ""; flex: 1; height: 1px; background: rgba(255,255,255,0.85);
  }
  .services-list {
    position: absolute; left: 0; right: 0; top: 380px; text-align: center;
    font-size: 17px; line-height: 25px;
  }
</style>
</head>
<body>
  <section class="card card-front">
    <div class="brand-block">
      <div class="brand-name"><span class="brand-mark"></span>Norrell Advisory</div>
      <div class="brand-tagline">Steady Steps Lasting Gains</div>
    </div>
    <div class="divider"></div>
    <div class="people">
      <div class="person-name">Derek Holloway</div>
      <div class="person-phone">0407385510</div>
      <div class="person-name">Megan Holloway</div>
      <div class="person-phone">0407913847</div>
    </div>
    <ul class="contact-list">
      <li class="contact-item">
        <svg class="contact-icon" viewBox="0 0 18 18" aria-hidden="true">
          <rect x="1" y="4" width="16" height="11" fill="#0a76b8"/>
          <path d="M1.5 4.5 L9 10.5 L16.5 4.5" fill="none" stroke="#fff" stroke-width="1.4"/>
        </svg>
        norrelladvisorywa@mailbox-example.com
      </li>
      <li class="contact-item">
        <svg class="contact-icon" viewBox="0 0 18 18" aria-hidden="true">
          <circle cx="9" cy="9" r="8" fill="#0a76b8"/>
          <ellipse cx="9" cy="9" rx="3.5" ry="8" fill="none" stroke="#fff" stroke-width="1.1"/>
          <line x1="1" y1="9" x2="17" y2="9" stroke="#fff" stroke-width="1.1"/>
        </svg>
        www.norrelladvisorywa-example.com
      </li>
      <li class="contact-item">
        <span class="contact-square"></span>
        norrelladvisorywa
      </li>
    </ul>
    <div class="front-rule"></div>
    <div class="front-band"></div>
  </section>

  <section class="card card-back">
    <div class="back-brand">Norrell Advisory</div>
    <div class="services-heading">Providing assistance with</div>
    <div class="services-list">
      Organisation &amp; Efficiency • Revenue generation &amp; Marketing • Financial Management<br>
      Production quality &amp; delivery • Systems &amp; Process documentation • Exit Strategy
    </div>
  </section>
</body>
</html>
```